Pine Hollow Haven Home Inc. Website Update

We have a couple of broken links such as the "contact us" and would like to add board members and a calendar of events. We are open to a new design.

```html
<!DOCTYPE html>
<html lang="en">
<head>
<meta charset="utf-8">
<title>Pine Hollow Haven Home Inc.</title>
<link href="https://fonts.googleapis.com/css2?family=Barlow:wght@400;500;600;700&family=Lato:wght@400;700&display=swap" rel="stylesheet">
<style>
:root{
  --pink:#d95879;
  --pink-dark:#c9466a;
  --blue:#1d5cb4;
  --blue-dark:#174a98;
  --ink:#222326;
  --text:#555;
  --grey-bg:#efefef;
  --orange:#f0a21d;
  --white:#fff;
}
*{margin:0;padding:0;box-sizing:border-box}
html,body{width:1200px;height:4557px;overflow:hidden}
body{position:relative;background:var(--white);font-family:'Lato',sans-serif;color:var(--text);font-size:13px;line-height:1.55}
.abs{position:absolute}
h1,h2,h3,h4{font-family:'Barlow',sans-serif;color:var(--ink);font-weight:600}
.btn{position:absolute;display:inline-block;border-radius:20px;color:var(--white);font-family:'Barlow',sans-serif;font-weight:600;font-size:12px;text-align:center;letter-spacing:.5px}
.btn-pink{background:var(--pink)}
.btn-blue{background:var(--blue)}
.photo{position:absolute}

/* header */
.topbar{top:0;left:0;width:1200px;height:36px;background:var(--pink)}
.topbar .phone{left:760px;top:9px;color:var(--white);font-family:'Barlow',sans-serif;font-weight:600;font-size:13px}
.topbar .donate{left:935px;top:6px;width:100px;height:24px;line-height:24px;background:var(--blue)}
.navbar{top:36px;left:0;width:1200px;height:84px;background:var(--white)}
.nav{left:395px;top:32px;display:flex;gap:18px;list-style:none;font-family:'Barlow',sans-serif;font-weight:600;font-size:13px;color:var(--ink)}
.logo{left:168px;top:0;width:172px;height:150px;border-radius:0 0 86px 86px;background:var(--white);border:4px solid var(--pink);border-top:none;display:flex;flex-direction:column;align-items:center;justify-content:center;z-index:2}
.logo .dot{width:26px;height:26px;border-radius:50%;background:var(--pink);margin-bottom:8px}
.logo .name{font-family:'Barlow',sans-serif;font-weight:700;font-size:14px;color:var(--pink);text-align:center;line-height:1.2}

/* hero */
.hero{top:120px;left:0;width:1200px;height:660px;background:linear-gradient(160deg,#4d6b2e 0%,#7a9a45 30%,#c9a58a 55%,#8fa6c8 80%,#3f5f8c 100%)}
.hero-wave{top:660px;left:0}

/* girls & mission */
.intro{top:800px;left:0;width:1200px;height:295px;background:var(--grey-bg)}
.intro h2{font-size:28px;position:absolute;top:25px}
.intro p{position:absolute;font-size:11.5px;line-height:1.45;width:215px;top:70px}
.circle-photo{border-radius:50%;border:4px solid var(--white);box-shadow:0 0 0 3px var(--pink)}

/* about */
.about h2{font-size:29px;line-height:1.18;font-weight:600}
.about .lead{font-size:14px;color:#777;width:420px}
.about .body{font-size:11.5px;width:420px;line-height:1.55}
.service{position:absolute;width:176px;height:178px;border:2px solid var(--pink);display:flex;flex-direction:column;align-items:center;justify-content:center;text-align:center;font-size:13.5px;color:var(--ink);line-height:1.35}
.service svg{margin-bottom:12px}

/* board */
.board-bg{top:1700px;left:0;width:1200px;height:640px;background:var(--grey-bg)}
.section-title{position:absolute;left:0;width:1200px;text-align:center;font-size:30px;letter-spacing:.5px}
.section-sub{position:absolute;left:400px;width:400px;text-align:center;font-size:13.5px;color:#777}
.member{position:absolute;width:190px;text-align:center}
.member .photo-ring{width:166px;height:160px;margin:0 auto;border-radius:50%;border:3px solid var(--pink);padding:5px;background:var(--white)}
.member .photo-ring div{width:100%;height:100%;border-radius:50%}
.member h4{color:var(--pink);font-size:15px;margin-top:18px}
.member p{font-size:11px;line-height:1.45;margin-top:4px}
.arrow{position:absolute}

/* calendar */
.cal{top:2565px;left:170px;width:322px;height:460px;background:var(--white);border:1px solid #ddd}
.cal-top{height:215px;background:linear-gradient(160deg,#2a6fcc,var(--blue-dark));text-align:center;color:var(--white);position:relative}
.cal-top .month{font-family:'Barlow',sans-serif;font-weight:600;font-size:30px;padding-top:52px}
.cal-top .year{font-size:14px}
.cal-top .add{left:111px;top:150px;width:100px;height:26px;line-height:26px;font-weight:500}
.cal-top .chev{position:absolute;top:62px;font-size:22px}
.cal-grid{display:grid;grid-template-columns:repeat(7,1fr);padding:20px 14px 0;row-gap:14px;text-align:center;font-size:14px;color:var(--ink)}
.cal-grid .dow{color:var(--pink);font-family:'Barlow',sans-serif;font-weight:600;font-size:12px}
.cal-grid .muted{color:#aaa}
.event{position:absolute;top:2565px;width:256px;height:460px;border:1px solid #ddd;background:var(--white)}
.event .img{height:210px}
.event h4{color:var(--pink);font-weight:500;font-size:16px;line-height:1.25;padding:22px 18px 10px}
.event p{font-size:11px;line-height:1.5;padding:0 18px}
.event .date{left:18px;bottom:36px;width:110px;height:26px;line-height:26px;border-radius:0;font-weight:500;font-size:11px}

/* voices & team */
.voices{top:3145px;left:0;width:600px;height:535px;background:var(--pink-dark)}
.team{top:3145px;left:600px;width:600px;height:535px;background:linear-gradient(135deg,#2367c2,var(--blue-dark))}
.band h2{color:var(--white);font-weight:500;font-size:29px;position:absolute;top:100px}
.band p{position:absolute;color:var(--white);font-size:11.5px;line-height:1.55}
.job{position:absolute;top:270px;width:188px;height:176px;background:var(--orange);border:3px solid #f6c25a;text-align:center;color:var(--white);padding-top:38px}
.job h4{color:var(--white);font-size:18px;line-height:1.2}
.job p{position:static;font-size:11px;margin-top:8px;line-height:1.4}

/* contact */
.contact h2{font-size:32px}
.field{position:absolute;left:385px;width:425px;border-bottom:1px solid #bbb;font-size:12px;color:var(--ink);padding-bottom:4px}

/* footer */
.footer-bg{top:4095px;left:0;width:1200px;height:462px}
.foot-logo{left:183px;top:4250px;width:170px;height:170px;border-radius:50%;background:var(--white);border:4px solid var(--pink);display:flex;flex-direction:column;align-items:center;justify-content:center}
.foot-col h3{color:var(--white);font-size:20px;font-weight:600}
.foot-col ul{list-style:none;margin-top:14px;color:var(--white);font-size:11.5px;line-height:1.65}
.foot-contact{color:var(--white);font-size:11.5px;line-height:1.45}
.social{position:absolute;top:4408px;width:26px;height:26px;border-radius:50%;background:var(--white)}
.copy{left:0;top:4514px;width:1200px;text-align:center;color:var(--white);font-size:11.5px}
</style>
</head>
<body>

<!-- header -->
<div class="abs topbar">
  <span class="abs phone">&#9742; CALL US: 770.555.0142</span>
  <span class="btn donate">DONATE NOW</span>
</div>
<div class="abs navbar">
  <ul class="abs nav">
    <li>HOME</li><li>ABOUT</li><li>HOW YOU CAN HELP</li><li>SERVICES OFFERED</li><li>OUR LOVE OF PETS</li><li>CONTACT US</li><li>HAVEN WALK</li>
  </ul>
</div>
<div class="abs logo">
  <span class="dot"></span>
  <span class="name">PINE HOLLOW<br>HAVEN HOME</span>
</div>

<!-- hero -->
<div class="photo hero" role="img" aria-label="Group of smiling girls lying in a circle on green grass, seen from above"></div>
<svg class="abs hero-wave" width="1200" height="150" viewBox="0 0 1200 150" aria-hidden="true">
  <path d="M0 40 C300 140 850 140 1200 30 L1200 150 L0 150 Z" fill="var(--blue)"/>
  <path d="M0 52 C300 150 850 150 1200 48 L1200 150 L0 150 Z" fill="var(--pink)"/>
  <path d="M0 64 C300 160 850 160 1200 64 L1200 150 L0 150 Z" fill="var(--grey-bg)"/>
</svg>

<!-- girls & mission -->
<section class="abs intro">
  <h2 style="left:240px;color:var(--pink)">OUR GIRLS</h2>
  <p style="left:168px;text-align:right">Lorem ipsum dolor sit amet, consectetur adipiscing elit, sed do eiusmod tempor incididunt ut labore et dolore mag</p>
  <span class="btn btn-pink" style="left:278px;top:135px;width:100px;height:26px;line-height:26px">LEARN ABOUT</span>
  <div class="photo circle-photo" role="img" aria-label="Photo of smiling girls together" style="left:408px;top:8px;width:176px;height:176px;background:linear-gradient(135deg,#8a6b5c,#d7b7a0 50%,#5f4a44)"></div>
  <div class="photo circle-photo" role="img" aria-label="Photo of a girl hugging a dog" style="left:620px;top:8px;width:176px;height:176px;background:linear-gradient(135deg,#cfc7bc,#8b8278 50%,#4c4640);box-shadow:0 0 0 3px var(--blue)"></div>
  <h2 style="left:815px;color:var(--blue)">OUR MISSION</h2>
  <p style="left:815px">Lorem ipsum dolor sit amet, consectetur adipiscing elit, sed do eiusmod tempor incididunt ut labore et dolore mag</p>
  <span class="btn btn-blue" style="left:818px;top:135px;width:100px;height:26px;line-height:26px">LEARN ABOUT</span>
</section>

<!-- about -->
<section class="about">
  <h2 class="abs" style="left:175px;top:1258px">WE ARE PINE HOLLOW<br>HAVEN HOME</h2>
  <p class="abs lead" style="left:175px;top:1345px">With the help of our community, we have raised over 1000 girls and counting! Some of the services we offer include:</p>
  <p class="abs body" style="left:175px;top:1405px">Lorem ipsum dolor sit amet, consectetur adipiscing elit, sed do eiusmod tempor incididunt ut labore et dolore magna aliqua. Ut enim ad minim veniam, quis nostrud exercitation ullamco laboris nisi ut aliquip ex ea commodo consequat. Duis aute irure dolor in reprehenderit in volupta</p>

  <div class="service" style="left:655px;top:1200px">
    <svg width="64" height="60" viewBox="0 0 64 60" fill="none" stroke="var(--pink)" stroke-width="2.5"><path d="M8 28 L32 8 L56 28"/><path d="M14 24 V54 H50 V24"/><path d="M32 46 C22 38 24 30 30 32 C31 32 32 34 32 35 C32 34 33 32 34 32 C40 30 42 38 32 46Z"/></svg>
    Room, Board, and<br>Watchful Oversight
  </div>
  <div class="service" style="left:848px;top:1200px">
    <svg width="70" height="60" viewBox="0 0 70 60" fill="none" stroke="var(--pink)" stroke-width="2.5"><path d="M26 52 C6 36 4 20 14 14 C20 10 26 14 28 20 C30 14 36 10 42 14 C52 20 48 36 26 52Z"/><path d="M44 42 C60 32 66 20 58 14 C54 11 48 13 46 18"/></svg>
    Transitional<br>Living Services
  </div>
  <div class="service" style="left:655px;top:1402px">
    <svg width="64" height="60" viewBox="0 0 64 60" fill="none" stroke="var(--pink)" stroke-width="2.5"><path d="M32 48 C14 34 14 20 24 18 C28 17 31 20 32 24 C33 20 36 17 40 18 C50 20 50 34 32 48Z"/><path d="M4 40 L18 52 H40"/><path d="M60 40 L46 52"/></svg>
    Independent<br>Living Services
  </div>
  <div class="service" style="left:848px;top:1402px">
    <svg width="64" height="60" viewBox="0 0 64 60" fill="none" stroke="var(--pink)" stroke-width="2.5"><path d="M32 50 C8 34 6 16 18 12 C25 10 30 14 32 20 C34 14 39 10 46 12 C58 16 56 34 32 50Z"/><path d="M20 30 L30 36 L44 24"/></svg>
    Foster<br>Gift Shop
  </div>
</section>

<!-- board -->
<svg class="abs" style="top:1640px;left:0" width="1200" height="70" viewBox="0 0 1200 70" aria-hidden="true">
  <path d="M0 30 C300 -5 700 70 1200 20 L1200 70 L0 70 Z" fill="var(--grey-bg)"/>
</svg>
<div class="abs board-bg"></div>
<svg class="abs" style="left:586px;top:1752px" width="28" height="24" viewBox="0 0 28 24" aria-hidden="true"><path d="M14 22 C2 13 2 5 8 3 C11 2 13 4 14 7 C15 4 17 2 20 3 C26 5 26 13 14 22Z" fill="none" stroke="var(--pink)" stroke-width="2.5"/></svg>
<h2 class="section-title" style="top:1788px">BOARD MEMBERS</h2>
<p class="section-sub" style="top:1838px">Lorem ipsum dolor sit amet, consectetur adipiscing elit, sed do eiusmod tempor incididunt ut labore et dolore magna aliqua.</p>
<svg class="arrow" style="left:108px;top:1995px" width="20" height="44" viewBox="0 0 20 44" aria-hidden="true"><path d="M18 2 L2 22 L18 42" fill="none" stroke="#999" stroke-width="2"/></svg>
<svg class="arrow" style="left:1070px;top:1995px" width="20" height="44" viewBox="0 0 20 44" aria-hidden="true"><path d="M2 2 L18 22 L2 42" fill="none" stroke="#999" stroke-width="2"/></svg>

<div class="member" style="left:172px;top:1940px"><div class="photo-ring"><div role="img" aria-label="Portrait of a board member" style="background:linear-gradient(180deg,#e9e4df,#b79a82)"></div></div><h4>Name: Loremiash</h4><p>Lorem ipsum dolor sit amet, nisi tortor adipiscing elit, sed do eiusm tempor.</p></div>
<div class="member" style="left:396px;top:1940px"><div class="photo-ring"><div role="img" aria-label="Portrait of a board member" style="background:linear-gradient(180deg,#9c9a99,#2f2d2d)"></div></div><h4>Name: Loremiash</h4><p>Lorem ipsum dolor sit amet, nisi tortor adipiscing elit, sed do eiusm tempor.</p></div>
<div class="member" style="left:620px;top:1940px"><div class="photo-ring"><div role="img" aria-label="Portrait of a board member" style="background:linear-gradient(180deg,#c9c6c2,#3a2f2a)"></div></div><h4>Name: Loremiash</h4><p>Lorem ipsum dolor sit amet, nisi tortor adipiscing elit, sed do eiusm tempor.</p></div>
<div class="member" style="left:843px;top:1940px"><div class="photo-ring"><div role="img" aria-label="Portrait of a board member" style="background:linear-gradient(180deg,#dfe3e8,#8ea0b8)"></div></div><h4>Name: Loremiash</h4><p>Lorem ipsum dolor sit amet, nisi tortor adipiscing elit, sed do eiusm tempor.</p></div>

<!-- calendar -->
<h2 class="section-title" style="top:2438px">CALENDAR OF EVENTS</h2>
<p class="section-sub" style="top:2490px">Lorem ipsum dolor sit amet, consectetur adipiscing elit, sed do eiusmod tempor incididunt ut labore et dolore magna aliqua.</p>

<div class="abs cal">
  <div class="cal-top">
    <span class="chev" style="left:58px">&#8249;</span><span class="chev" style="right:58px">&#8250;</span>
    <div class="month">MARCH</div>
    <div class="year">2019</div>
    <span class="btn btn-pink add">ADD EVENT</span>
  </div>
  <div class="cal-grid">
    <span class="dow">SUN</span><span class="dow">MON</span><span class="dow">TUE</span><span class="dow">WED</span><span class="dow">THU</span><span class="dow">FRI</span><span class="dow">SAT</span>
    <span class="muted">28</span><span class="muted">29</span><span class="muted">30</span><span class="muted">31</span><span>1</span><span>2</span><span>3</span>
    <span>4</span><span>5</span><span>6</span><span>7</span><span>8</span><span>9</span><span>10</span>
    <span>11</span><span>12</span><span>13</span><span>14</span><span>15</span><span>16</span><span>17</span>
    <span>18</span><span>19</span><span>20</span><span>21</span><span>22</span><span>23</span><span>24</span>
    <span>25</span><span>26</span><span>27</span><span>28</span><span>29</span><span>30</span><span>31</span>
  </div>
</div>

<div class="event" style="left:505px">
  <div class="img" role="img" aria-label="Women gathered around a table at an event" style="background:linear-gradient(135deg,#e4e2e0,#b9a79a 50%,#7b6a62)"></div>
  <h4>Lorem ipsum dolor sit amet, consectetur adipiscing e</h4>
  <p>Lorem ipsum dolor sit amet, consectetur ipsum elit, sed do eiusmod tempor incididunt ut labore et dolore magna aliquat enim ad minim veniam, quis nostrud.</p>
  <span class="btn btn-blue date">March 07 2019</span>
</div>
<div class="event" style="left:773px">
  <div class="img" role="img" aria-label="Friends talking at a cafe table" style="background:linear-gradient(135deg,#3d2a22,#7a5a44 50%,#c29a74)"></div>
  <h4>Lorem ipsum dolor sit amet, consectetur adipiscing e</h4>
  <p>Lorem ipsum dolor sit amet, consectetur ipsum elit, sed do eiusmod tempor incididunt ut labore et dolore magna aliquat enim ad minim veniam, quis nostrud.</p>
  <span class="btn btn-blue date">March 07 2019</span>
</div>

<!-- voices & team -->
<section class="abs band voices">
  <h2 style="left:175px">WHAT OUR GIRLS SAY</h2>
  <p style="left:175px;top:158px;width:370px">If you're a former resident of the Haven Home and would like to tell us about your experience, please email us at info@pinehollowhaven.org or come by and see us! You can also friend us on social media, we love to keep in touch!</p>
  <span class="abs" style="left:175px;top:260px;color:var(--white);font-size:34px;font-family:'Barlow',sans-serif;font-weight:700;line-height:1">&#8220;</span>
  <p style="left:205px;top:268px;width:340px">I was lonely, tired, and lost when I first arrived. I learned how to cook, budget, get a job, buy a car, pay bills, community service and helping others. I would not have gotten here without the Haven House.</p>
  <p style="left:175px;top:390px;font-size:13px">~Marisol</p>
  <span class="abs" style="left:200px;top:455px;color:var(--white);font-size:22px">&#8249; &#8250;</span>
</section>
<section class="abs band team">
  <h2 style="left:30px">JOIN OUR TEAM!</h2>
  <p style="left:30px;top:158px;width:380px">Sed ut perspiciatis unde omnis iste natus error sit voluptatem accusantium doloremque laudantium, totam rem aperiam, eaque ipsa quae ab illo inve ntore veritatis et quasi architecto beatae vitae dicta sunt.</p>
  <div class="job" style="left:30px"><h4>Overnight Shift<br>House Parent</h4><p>Oakvale, GA  |  Temporary<br>Salary: $15.50 / Hour</p></div>
  <div class="job" style="left:240px"><h4>Direct Care<br>Worker (DCW)</h4><p>Oakvale, GA  |  Full time</p></div>
</section>

<!-- contact -->
<section class="contact">
  <h2 class="abs" style="left:0;width:1200px;text-align:center;top:3752px">CONTACT US</h2>
  <p class="abs" style="left:400px;width:400px;text-align:center;top:3800px;font-size:11.5px">Sed ut perspiciatis unde omnis iste natus error sit voluptatem accusantium doloremque laudantium, totam rem aperiam, eaque ipsa quae.</p>
  <div class="field" style="top:3862px">Name:</div>
  <div class="field" style="top:3905px">Email:</div>
  <div class="field" style="top:3950px">Phone:</div>
  <div class="field" style="top:3993px;height:52px">Message:</div>
  <span class="btn btn-pink" style="left:545px;top:4065px;width:106px;height:36px;line-height:36px;font-size:13px">SUBMIT</span>
  <div class="photo" role="img" aria-label="Smiling woman in a dark blazer pointing toward the form" style="left:830px;top:3695px;width:300px;height:470px;border-radius:140px 140px 30px 30px;background:linear-gradient(180deg,#5a3a2c 0%,#d8b09a 30%,#2a2a30 55%,#151518 100%)"></div>
</section>

<!-- footer -->
<svg class="abs footer-bg" width="1200" height="462" viewBox="0 0 1200 462" aria-hidden="true">
  <defs><linearGradient id="footGrad" x1="0" y1="0" x2="0" y2="1"><stop offset="0" stop-color="#d9597b"/><stop offset="0.45" stop-color="#b25a95"/><stop offset="1" stop-color="#2a5cb8"/></linearGradient></defs>
  <path d="M0 50 C350 -10 750 120 1200 20 L1200 462 L0 462 Z" fill="url(#footGrad)"/>
</svg>
<div class="abs foot-logo"><span class="logo-dot" style="width:26px;height:26px;border-radius:50%;background:var(--pink);margin-bottom:8px"></span><span style="font-family:'Barlow',sans-serif;font-weight:700;font-size:14px;color:var(--pink);text-align:center;line-height:1.2">PINE HOLLOW<br>HAVEN HOME</span></div>

<div class="abs foot-col" style="left:470px;top:4245px">
  <h3>Links</h3>
  <ul><li>Home</li><li>About</li><li>How You Can Help</li><li>Services Offered</li><li>Our Love of Pets</li><li>Contact Us</li><li>Haven Walk</li></ul>
</div>
<div class="abs foot-col" style="left:630px;top:4245px">
  <h3>Contact Us</h3>
</div>
<svg class="abs" style="left:632px;top:4296px" width="16" height="20" viewBox="0 0 16 20" aria-hidden="true"><path d="M8 19 C3 12 1 9 1 7 A7 7 0 0 1 15 7 C15 9 13 12 8 19Z" fill="none" stroke="#fff" stroke-width="1.6"/><circle cx="8" cy="7" r="2.5" fill="none" stroke="#fff" stroke-width="1.6"/></svg>
<p class="abs foot-contact" style="left:668px;top:4294px">1200 Ridgeline Rd, Oakvale,<br>GA 30999, USA</p>
<svg class="abs" style="left:631px;top:4348px" width="18" height="18" viewBox="0 0 18 18" aria-hidden="true"><path d="M4 1 L7 5 L5 7 C6 10 8 12 11 13 L13 11 L17 14 L15 17 C8 17 1 10 1 3Z" fill="none" stroke="#fff" stroke-width="1.6"/></svg>
<p class="abs foot-contact" style="left:668px;top:4344px">Phone:<br>770.555.0142</p>
<svg class="abs" style="left:630px;top:4398px" width="20" height="14" viewBox="0 0 20 14" aria-hidden="true"><rect x="1" y="1" width="18" height="12" fill="none" stroke="#fff" stroke-width="1.6"/><path d="M1 1 L10 8 L19 1" fill="none" stroke="#fff" stroke-width="1.6"/></svg>
<p class="abs foot-contact" style="left:668px;top:4392px">Email:<br>info@pinehollowhaven.org</p>

<div class="abs" role="img" aria-label="Anniversary badge" style="left:873px;top:4248px;width:120px;height:120px;border-radius:50%;background:radial-gradient(circle,#f3c64a,#c98f16)"></div>
<span class="social" style="left:860px"></span>
<span class="social" style="left:900px"></span>
<span class="social" style="left:940px"></span>
<span class="social" style="left:980px"></span>

<p class="abs copy">&copy; 2019 All Rights Are Reserved Terms of Use | Privacy Policy</p>

</body>
</html>
```